Dental Implant Logo and Business Card for Local Dentist

Design a unique business card and a logo that incorporates a dental implant as a primary focal point or a part of the text. New logo design & business card needs to incorporate our businesses old star shaped logo (attached) and a dental implant, along with our business name. Star logo does not have to remain the exact same colors and can be any size. Looking for a warm, friendly (non-aggressive) design that uses colors in the blue-green palate, partial to mint-turquoise color similar to the images attached . SIMPLE IS GOOD, but looking for creativity to bring all the elements together. OK to incorporate a splash of color. I have attached a few images of implant logos I like along with our existing star shaped logo. *I have also uploaded some images that represent local landscapes & images for the back of the business card. I would like to include a silhouette or sketch that represents one one of these areas on the back of the business card to convey the connection to our community and local roots of our business since we are 4th generation members of this community . Can visit our dental practice website for more info. www.hartwellandodegarddentalcare.example Card Must Haves on Front of Card:1. business name "Hartwell & Odegard Dental Care" 2. My Name: "Colin Odegard D.D.S."3. Phone # (925) 754-6020Other info for card (can be front or back)Address: 7840 Quarry Ridge Rd. #2C Larkspur Bay, Ca 94531e-mail: millerandsimarrodentalcare@gmail.comcosmetic, family, & impDesign a unique business card and a logo that incorporates a dental implant as a primary focal point or a part of the text. New logo design & business card needs to incorporate our businesses old star shaped logo (attached) and a dental implant, along with our business name. Star logo does not have to remain the exact same colors and can be any size. Looking for a warm, friendly (non-aggressive) design that uses colors in the blue-green palate, partial to mint-turquoise color similar to the images attached . SIMPLE IS GOOD, but looking for creativity to bring all the elements together. OK to incorporate a splash of color. I have attached a few images of implant logos I like along with our existing star shaped logo. *I have also uploaded some images that represent local landscapes & images for the back of the business card. I would like to include a silhouette or sketch that represents one one of these areas on the back of the business card to convey the connection to our community and local roots of our business since we are 4th generation members of this community . Can visit our dental practice website for more info. www.hartwellandodegarddentalcare.example Card Must Haves on Front of Card:1. business name "Hartwell & Odegard Dental Care" 2. My Name: "Colin Odegard D.D.S."3. Phone # (925) 754-6020Other info for card (can be front or back)Address: 7840 Quarry Ridge Rd. #2C Larkspur Bay, Ca 94531e-mail: millerandsimarrodentalcare@gmail.comcosmetic, family, & implant dentistry

Target Market(s)

Families

Industry/Entity Type

Dental

Contact Information for Business Card

See Project description above

Logo Text

Hartwell & Odegard Dental Care

Font styles to use
Serif

Colors
ffffff
33b8a4
87cfc6
0492cd
33a6d7
0255a3

Requirements
Must have
• *See Description...
• Card Must Haves on Front of Card:
• 1. business name "Hartwell & Odegard Dental Care"
• 2. My Name: "Colin Odegard D.D.S."
• 3. Phone # (555) 318-4297
• Other info for card (can be front or back)
• Address: 7840 Quarry Ridge Rd. #2C Larkspur Bay, Ca 90217
• e-mail: hartwellandodegarddentalcare@example-mail.com
Nice to have
• Local image sketch or silhouette on back side of business card with remaining information on back: address, website, e-mail etc.

```html
<!DOCTYPE html>
<html lang="en">
<head>
<meta charset="utf-8">
<title>Hartwell &amp; Odegard Dental Care — Business Card</title>
<link rel="stylesheet" href="https://fonts.googleapis.com/css2?family=Cinzel:wght@400;600&family=Lato:wght@400;700&display=swap">
<style>
  :root {
    --bg: #8a8784;
    --blue: #1a93d1;
    --blue-deep: #0b84c6;
    --teal: #33b8a4;
    --white: #ffffff;
    --ink: #2b2b2b;
  }
  * { box-sizing: border-box; margin: 0; padding: 0; }
  html, body { width: 1200px; height: 858px; overflow: hidden; }
  body {
    background: var(--bg);
    position: relative;
    font-family: "Lato", sans-serif;
  }
  .card {
    position: absolute;
    top: 279px;
    width: 520px;
    height: 300px;
    border-radius: 26px;
    overflow: hidden;
    box-shadow: 0 6px 18px rgba(0,0,0,0.25);
  }

  /* Logo side */
  .card-logo-side {
    left: 50px;
    background: var(--blue);
    color: var(--white);
    text-align: center;
  }
  .brand-block {
    position: absolute;
    left: 0; right: 0;
    top: 96px;
    font-family: "Cinzel", serif;
    font-weight: 600;
  }
  .brand-name {
    font-size: 27px;
    letter-spacing: 1px;
    line-height: 1;
  }
  .brand-sub {
    display: flex;
    align-items: center;
    justify-content: center;
    gap: 10px;
    margin-top: 8px;
    font-size: 11px;
    letter-spacing: 5px;
  }
  .brand-sub .rule { width: 70px; height: 1.5px; background: var(--white); }
  .tagline {
    position: absolute;
    left: 0; right: 0;
    top: 200px;
    font-size: 17px;
    letter-spacing: 1px;
  }

  /* Contact side */
  .card-contact-side {
    left: 630px;
    background: var(--white);
  }
  .person-name {
    position: absolute;
    left: 38px;
    top: 62px;
    font-family: "Cinzel", serif;
    font-weight: 600;
    font-size: 22px;
    color: var(--blue-deep);
    letter-spacing: 0.5px;
  }
  .side-tab {
    position: absolute;
    left: 0; top: 64px;
    width: 6px; height: 24px;
    background: var(--teal);
  }
  .corner-brand {
    position: absolute;
    right: 34px;
    top: 34px;
    display: flex;
    align-items: center;
    gap: 8px;
    font-family: "Cinzel", serif;
    font-weight: 600;
    font-size: 15px;
    color: var(--blue-deep);
  }
  .corner-brand .dot {
    width: 16px; height: 16px;
    border-radius: 50%;
    background: var(--teal);
  }
  .address {
    position: absolute;
    right: 34px;
    top: 118px;
    text-align: left;
    font-style: normal;
    font-size: 14px;
    line-height: 1.35;
    color: var(--ink);
  }
  .address .practice {
    font-family: "Cinzel", serif;
    font-style: normal;
    color: var(--teal);
    font-size: 15px;
  }
  .contact-list {
    position: absolute;
    left: 40px;
    bottom: 40px;
    list-style: none;
    font-size: 13.5px;
    color: var(--ink);
  }
  .contact-list li {
    display: flex;
    align-items: center;
    gap: 10px;
    line-height: 1.55;
  }
  .contact-list svg { width: 13px; height: 13px; fill: var(--blue-deep); flex: none; }
  .bottom-band {
    position: absolute;
    left: 0; right: 0; bottom: 0;
    height: 8px;
    display: flex;
  }
  .bottom-band .teal { flex: 3; background: var(--teal); }
  .bottom-band .gap { width: 4px; background: var(--white); }
  .bottom-band .blue { flex: 1; background: var(--blue-deep); }
</style>
</head>
<body>

<section class="card card-logo-side" aria-label="Card logo side">
  <div class="brand-block">
    <div class="brand-name">HARTWELL &amp; ODEGARD</div>
    <div class="brand-sub">
      <span class="rule"></span><span class="label">DENTAL CARE</span><span class="rule"></span>
    </div>
  </div>
  <p class="tagline">Family, &amp; implant dentistry</p>
</section>

<section class="card card-contact-side" aria-label="Card contact side">
  <span class="side-tab"></span>
  <h1 class="person-name">COLIN ODEGARD D.D.S.</h1>

  <div class="corner-brand"><span class="dot"></span>Hartwell &amp; Odegard</div>

  <address class="address">
    <div class="practice">Hartwell &amp; Odegard</div>
    7840 Quarry Ridge,<br>
    Rd. #2C, Larkspur Bay, Ca 90217
  </address>

  <ul class="contact-list">
    <li>
      <svg viewBox="0 0 24 24" aria-hidden="true"><path d="M6.6 10.8a15.1 15.1 0 0 0 6.6 6.6l2.2-2.2c.3-.3.7-.4 1-.2 1.1.4 2.3.6 3.6.6.6 0 1 .4 1 1V20c0 .6-.4 1-1 1A17 17 0 0 1 3 4c0-.6.4-1 1-1h3.5c.6 0 1 .4 1 1 0 1.3.2 2.5.6 3.6.1.3 0 .7-.2 1z"/></svg>
      (555) 318-4297
    </li>
    <li>
      <svg viewBox="0 0 24 24" aria-hidden="true"><path d="M2 5h20v14H2z M2 5l10 8 10-8" /></svg>
      hartwellandodegarddentalcare@example-mail.com
    </li>
    <li>
      <svg viewBox="0 0 24 24" aria-hidden="true"><circle cx="12" cy="12" r="10"/></svg>
      www.hartwellandodegarddentalcare.example
    </li>
  </ul>

  <div class="bottom-band"><span class="teal"></span><span class="gap"></span><span class="blue"></span></div>
</section>

</body>
</html>
```